Sleek wordpress site for Bramblecrest finishing works

We are a commercial job shop that serves B2B, govt & LEO and retail clients.We need a wordpress site with 6 individual pages: homepage, coating, laser engraving, laser cutting, part marking, and contact us. I have attached an outline of the desired flow and sub headings for each page. I would like to incorporate the colors of the logo through out the site to be clean and sleek enough to appeal to B2B commercial clients yet be inviting enough for retail clients.

I would like to have easy picture functionality so photographs on each page can be updated easily.

Target Market(s)

B2B industrial & Govt and Military part marking, laser engraving and coating: machine shops, aerospace companies, tool manufactures. Retail: personalized gifts, Job Shop

Coding

Coded - Design and coding required

Font styles to use
Sans Serif
Other font styles liked:
• Open to suggestion

Colors
0255a3
3176b5
eaf1f7
cfdeed
ffffff

Requirements
Must have
• Clean easy to navigate flow, separate pages as indicated on attached outline, high class feel. Great picture functionality, professional and inviting feel,
• **update: needs to be optimized for mobile, should have a gallery function. Gallery can be an additional page or embedded
Nice to have
• Social media connectivity links,
Should not have
• crappy plugins that make back-end management difficult, no blog

```html
<!DOCTYPE html>
<html lang="en">
<head>
<meta charset="utf-8">
<title>Bramblecrest Finishing Works</title>
<link href="https://fonts.googleapis.com/css2?family=Lato:wght@400;700;900&family=Open+Sans:ital,wght@0,400;0,600;0,700;1,400&display=swap" rel="stylesheet">
<style>
:root{
  --blue:#0255a3;
  --blue-deep:#123f8c;
  --blue-mid:#3176b5;
  --pale:#eaf1f7;
  --pale-2:#cfdeed;
  --white:#ffffff;
  --ink:#1d1d1d;
  --grey:#666a70;
  --line:#9a9a9a;
}
*{box-sizing:border-box;margin:0;padding:0}
html,body{width:1200px;height:3125px;overflow:hidden}
body{position:relative;background:var(--white);font-family:'Open Sans',sans-serif;color:var(--ink)}
.abs{position:absolute}

/* hero */
.hero{left:0;top:0;width:1200px;height:633px;background:
  radial-gradient(ellipse at 55% 85%,rgba(255,150,50,.75),rgba(180,70,60,.3) 35%,transparent 60%),
  linear-gradient(160deg,#2c2747 0%,#4b3558 40%,#7a4a4e 70%,#2c2030 100%)}
.brand{left:100px;top:52px;display:flex;align-items:center;gap:12px;font-family:'Lato',sans-serif;font-weight:900;font-size:21px;line-height:1.05;color:var(--white);text-transform:uppercase;letter-spacing:.5px}
.brand-mark{width:42px;height:42px;border:3px solid var(--white);border-radius:50%}
.phone{right:68px;top:20px;color:var(--white);font-weight:700;font-size:17px;display:flex;align-items:center;gap:8px}
.nav{left:444px;top:62px;display:flex;gap:24px;font-family:'Lato',sans-serif;font-weight:700;font-size:16px;color:var(--white);align-items:center}
.nav .active{color:#4f8fdc}
.hero-title{left:0;width:1200px;top:222px;text-align:center;color:var(--white);font-family:'Lato',sans-serif;font-weight:900;font-size:44px;letter-spacing:.5px}
.hero-sub{left:0;width:1200px;top:298px;text-align:center;color:var(--white);font-size:21px}
.btn-ghost{left:502px;top:362px;width:195px;height:58px;border:2px solid var(--white);border-radius:30px;color:var(--white);font-weight:700;font-size:16px;display:flex;align-items:center;justify-content:center;text-transform:uppercase}
.dots{left:566px;top:561px;display:flex;gap:5px}
.dots span{width:12px;height:12px;border:2px solid var(--white);border-radius:50%}
.dots span:first-child{background:var(--white)}

/* partners */
.partner{top:645px;width:187px;height:148px;border:1px solid #bdbdbd;display:flex;align-items:center;justify-content:center}
.partner i{display:block;width:110px;height:26px;background:#c9cbcf;border-radius:4px}
.arrow{top:728px;width:40px;height:40px;border:2px solid #9a9a9a;border-radius:50%;display:flex;align-items:center;justify-content:center}

/* welcome */
.welcome{left:98px;top:883px;width:596px;height:452px;border:2px solid #8a8a8a;padding:40px 46px}
.welcome h2{font-family:'Lato',sans-serif;font-weight:900;font-size:36px;line-height:1.35;text-transform:uppercase;margin-bottom:22px}
.welcome p{font-size:14px;line-height:1.9;color:var(--grey);margin-bottom:22px;max-width:440px}
.btn{display:inline-flex;align-items:center;justify-content:center;background:var(--blue);color:var(--white);font-weight:700;font-size:15px;border-radius:30px;text-transform:uppercase}
.welcome .btn{width:144px;height:54px;margin-top:2px}
.video{left:634px;top:942px;width:466px;height:336px;background:linear-gradient(135deg,#c7cdd3,#8b9299 60%,#4d5258);box-shadow:0 6px 18px rgba(0,0,0,.3)}
.play{left:836px;top:1074px;width:64px;height:64px;border-radius:50%;background:#111;display:flex;align-items:center;justify-content:center}

/* services */
.services{left:0;top:1427px;width:1200px;height:691px;background:var(--pale)}
.section-title{left:0;width:1200px;text-align:center;font-family:'Lato',sans-serif;font-weight:900;font-size:36px;text-transform:uppercase}
.tile{top:1592px;width:252px;height:223px;clip-path:polygon(0 0,90% 0,100% 18%,100% 82%,90% 100%,0 100%,0 0)}
.tile.mid{clip-path:polygon(10% 0,90% 0,100% 18%,100% 82%,90% 100%,10% 100%,0 82%,0 18%)}
.tile.last{clip-path:polygon(10% 0,100% 0,100% 100%,10% 100%,0 82%,0 18%)}
.service{top:1848px;width:250px;text-align:center}
.service h3{font-family:'Lato',sans-serif;font-weight:700;font-size:23px;margin-bottom:12px}
.service p{font-size:14px;line-height:1.7;color:var(--grey);padding:0 20px;height:74px}
.plus{display:inline-flex;width:22px;height:22px;border-radius:50%;background:var(--blue);color:var(--white);font-weight:700;font-size:19px;align-items:center;justify-content:center;line-height:1;margin-top:26px}

/* testimonials */
.testimonials{left:0;top:2118px;width:1200px;height:492px;background:linear-gradient(135deg,#1a4c9c,var(--blue-deep) 60%,#164590)}
.quote{top:2323px;width:309px;height:199px;border:2px solid var(--white);text-align:center;color:var(--white);padding:62px 18px 0}
.quote p{font-style:italic;font-size:13px;line-height:1.9}
.quote h4{font-weight:600;font-size:18px;margin-top:12px}
.avatar{top:2278px;width:90px;height:90px;border-radius:50%;border:3px solid var(--white);background:linear-gradient(160deg,#c9ccd2,#7d858f)}

/* contact */
.contact-h{font-family:'Lato',sans-serif;font-weight:700;font-size:20px;text-transform:uppercase}
.field{border:1px solid #8a8a8a;height:32px;font-size:12px;color:#666;padding:8px 14px}
.info-row{left:778px;display:flex;align-items:center;gap:18px;font-size:13px;color:#333}
.ico{width:32px;height:32px;border:1px solid #bbb;border-radius:50%;display:flex;align-items:center;justify-content:center}
.social{top:2962px;width:32px;height:32px;border-radius:50%}
.rule{left:96px;top:3038px;width:1004px;height:1px;background:#bbb}
.copy{left:0;width:1200px;top:3068px;text-align:center;font-size:12px;color:#444}
</style>
</head>
<body>

<div class="abs hero" role="img" aria-label="Laser cutting head sending bright orange sparks across a metal sheet"></div>
<div class="abs brand"><span class="brand-mark"></span><span>Bramblecrest<br>Finishing Works</span></div>
<div class="abs phone">
  <svg width="16" height="16" viewBox="0 0 24 24" fill="#fff"><path d="M6.6 10.8a15 15 0 0 0 6.6 6.6l2.2-2.2c.3-.3.7-.4 1-.2 1.1.4 2.3.6 3.6.6.6 0 1 .4 1 1V20c0 .6-.4 1-1 1A17 17 0 0 1 3 4c0-.6.4-1 1-1h3.5c.6 0 1 .4 1 1 0 1.3.2 2.5.6 3.6.1.3 0 .7-.2 1z"/></svg>
  555.014.2290
</div>
<nav class="abs nav">
  <span class="active">Home</span><span>Coating</span><span>Laser Engraving</span><span>Laser Cutting</span><span>Part Marking</span><span>Contact us</span>
  <svg width="16" height="16" viewBox="0 0 24 24" fill="none" stroke="#fff" stroke-width="3"><circle cx="10" cy="10" r="7"/><path d="M15 15l6 6"/></svg>
</nav>
<h1 class="abs hero-title">COATINGS. PART MARKING. ENGRAVING</h1>
<p class="abs hero-sub">We are commercial job shop that serves B2B, govt and retail clients</p>
<div class="abs btn-ghost">Get more info</div>
<div class="abs dots"><span></span><span></span><span></span><span></span></div>

<div class="abs arrow" style="left:34px"><svg width="12" height="14" viewBox="0 0 12 14"><path d="M9 1L3 7l6 6" fill="none" stroke="#666" stroke-width="2"/></svg></div>
<div class="abs partner" style="left:98px"><i></i></div>
<div class="abs partner" style="left:302px"><i></i></div>
<div class="abs partner" style="left:507px"><i></i></div>
<div class="abs partner" style="left:711px"><i></i></div>
<div class="abs partner" style="left:915px"><i></i></div>
<div class="abs arrow" style="left:1125px"><svg width="12" height="14" viewBox="0 0 12 14"><path d="M3 1l6 6-6 6" fill="none" stroke="#666" stroke-width="2"/></svg></div>

<section class="abs welcome">
  <h2>Welcome to<br>Bramblecrest Finishing</h2>
  <p>Nemo enim ipsam voluptatem quia voluptas sit aspernatur autodit aut fugit, sed quia consequuntur mag.</p>
  <p>Dolores eos qui ratione voluptatem sequi nesciunt. Neque porrqu isquam est, qui dolorem ipsum quia dolor sit amet, consecteturadi pisci velit, sed quia non numquam eius.</p>
  <span class="btn">Read more</span>
</section>
<div class="abs video" role="img" aria-label="Video still of an operator checking a tablet beside a laser machine"></div>
<div class="abs play"><svg width="24" height="26" viewBox="0 0 24 26"><path d="M4 2l18 11L4 24z" fill="#fff"/></svg></div>

<section class="abs services"></section>
<h2 class="abs section-title" style="top:1500px">Our Services</h2>
<div class="abs tile" style="left:98px;background:linear-gradient(135deg,#2b2f3a,#5a4e4a 60%,#1c1f26)" role="img" aria-label="Laser engraving head with sparks"></div>
<div class="abs tile mid" style="left:348px;background:radial-gradient(circle at 55% 65%,#f0a040,#7a4a2e 45%,#222 80%)" role="img" aria-label="Laser cutter throwing sparks off a metal plate"></div>
<div class="abs tile mid" style="left:598px;background:linear-gradient(135deg,#3f77b8,#a9b2bb 50%,#5e6a58)" role="img" aria-label="Machined part clamped in a chuck for marking"></div>
<div class="abs tile last" style="left:848px;background:linear-gradient(135deg,#6a6e74,#d6d6d4 50%,#8b2a2a)" role="img" aria-label="Gloved hands spraying a ceramic coating"></div>

<div class="abs service" style="left:98px"><h3>Laser Engraving</h3><p>With our selection of CO2 and fiber lasers there are very few materials and substrates</p><span class="plus">+</span></div>
<div class="abs service" style="left:348px"><h3>Laser Cutting</h3><p>We can custom cut virtually any shape or design in a variety of substrates or materials.</p><span class="plus">+</span></div>
<div class="abs service" style="left:598px"><h3>Part Marking</h3><p>We will sample cut a piece of your material at no charge. Our cutting charges are based</p><span class="plus">+</span></div>
<div class="abs service" style="left:848px"><h3>Coating</h3><p>Duraglaze is a spray on ceramic based finish that can be applied to metals, plastics, polymers</p><span class="plus">+</span></div>

<section class="abs testimonials"></section>
<h2 class="abs section-title" style="top:2195px;color:var(--white)">Testimonials</h2>
<div class="abs quote" style="left:98px"><p>Nam libero tempore, cum soluta nobis est eligendi optio cumque nihil impedit quo minus id quod maxime placea</p><h4>Nora Fenwick</h4></div>
<div class="abs quote" style="left:446px"><p>Nam libero tempore, cum soluta nobis est eligendi optio cumque nihil impedit quo minus id quod maxime placea</p><h4>Tessa Marlowe</h4></div>
<div class="abs quote" style="left:794px"><p>Nam libero tempore, cum soluta nobis est eligendi optio cumque nihil impedit quo minus id quod maxime placea</p><h4>Owen Bracken</h4></div>
<div class="abs avatar" style="left:208px" role="img" aria-label="Client portrait"></div>
<div class="abs avatar" style="left:556px" role="img" aria-label="Client portrait"></div>
<div class="abs avatar" style="left:904px" role="img" aria-label="Client portrait"></div>

<h3 class="abs contact-h" style="left:94px;top:2704px">Contact Form</h3>
<div class="abs field" style="left:96px;top:2769px;width:310px">Name :</div>
<div class="abs field" style="left:415px;top:2769px;width:309px">Phone no :</div>
<div class="abs field" style="left:96px;top:2814px;width:628px">Email :</div>
<div class="abs field" style="left:96px;top:2860px;width:628px;height:82px">Message :</div>
<span class="abs btn" style="left:630px;top:2955px;width:94px;height:36px;font-size:14px">Submit</span>

<h3 class="abs contact-h" style="left:778px;top:2704px">Contact Information</h3>
<div class="abs info-row" style="top:2756px"><span class="ico"><svg width="12" height="16" viewBox="0 0 12 16"><path d="M6 0a6 6 0 0 0-6 6c0 4.5 6 10 6 10s6-5.5 6-10a6 6 0 0 0-6-6zm0 8.5A2.5 2.5 0 1 1 6 3.5a2.5 2.5 0 0 1 0 5z" fill="#0255a3"/></svg></span>418 N Alder Way #7, Fairhollow, AZ 85011</div>
<div class="abs info-row" style="top:2813px"><span class="ico"><svg width="14" height="14" viewBox="0 0 24 24" fill="#0255a3"><path d="M6.6 10.8a15 15 0 0 0 6.6 6.6l2.2-2.2c.3-.3.7-.4 1-.2 1.1.4 2.3.6 3.6.6.6 0 1 .4 1 1V20c0 .6-.4 1-1 1A17 17 0 0 1 3 4c0-.6.4-1 1-1h3.5c.6 0 1 .4 1 1 0 1.3.2 2.5.6 3.6.1.3 0 .7-.2 1z"/></svg></span>555.014.2290</div>
<div class="abs info-row" style="top:2864px"><span class="ico"><svg width="14" height="11" viewBox="0 0 14 11"><rect width="14" height="11" rx="1" fill="#0255a3"/><path d="M1 1l6 5 6-5" fill="none" stroke="#fff" stroke-width="1.3"/></svg></span>hello@bramblecrestworks.com</div>
<h3 class="abs contact-h" style="left:778px;top:2914px">Social Media</h3>
<span class="abs social" style="left:780px;background:#2d4c8e"></span>
<span class="abs social" style="left:822px;background:#2a9fd8"></span>
<span class="abs social" style="left:865px;background:#1a6fa3"></span>
<span class="abs social" style="left:908px;background:#c91f2a"></span>

<div class="abs rule"></div>
<p class="abs copy">Copyright © 2018, Bramblecrest Finishing. All rights reserved.</p>
<svg class="abs" style="left:1070px;top:3074px" width="28" height="16" viewBox="0 0 28 16"><path d="M2 14L14 3l12 11" fill="none" stroke="#999" stroke-width="3"/></svg>

</body>
</html>
```